business card deign

Logo needs the following on it.
1. attached logo
2. Tagline - "If it keeps a drink cold or the party going...we do it!"
3. Name- Dalton Pikes, Founder and CPO
4. Address - 412 E. Carver Avenue, Ste 2207, Tampa, FL. 33917
5. Phone - 555.318.4726

```html
<!DOCTYPE html>
<html lang="en">
<head>
<meta charset="utf-8">
<title>Kipsy Business Card</title>
<link href="https://fonts.googleapis.com/css2?family=Open+Sans:wght@400;700&display=swap" rel="stylesheet">
<style>
  :root {
    --backdrop: #232323;
    --card: #141414;
    --card-edge: #0a0a0a;
    --ink: #ffffff;
    --ink-soft: #e6e6e6;
  }
  * { margin: 0; padding: 0; box-sizing: border-box; }
  html, body {
    width: 1200px; height: 711px; overflow: hidden;
    background: var(--backdrop);
    font-family: "Open Sans", Arial, sans-serif;
    color: var(--ink);
  }
  .stage {
    width: 1200px; height: 711px;
    display: flex; align-items: center; justify-content: center; gap: 40px;
  }
  .card {
    position: relative;
    width: 540px; height: 309px;
    background: var(--card);
    border-radius: 26px;
    box-shadow: 0 14px 30px rgba(0,0,0,.55), 0 0 0 1px var(--card-edge);
    overflow: hidden;
  }
  .brand {
    display: flex; align-items: center; gap: 14px;
    font-weight: 700; letter-spacing: .28em; color: var(--ink);
  }
  .brand-dot {
    width: 18px; height: 18px; border-radius: 50%; background: var(--ink);
  }
  .card-front { display: flex; align-items: center; justify-content: center; }
  .card-front .brand { font-size: 44px; }
  .card-front .brand-dot { width: 26px; height: 26px; }

  .card-back .brand {
    position: absolute; top: 62px; right: 44px; font-size: 30px;
  }
  .details {
    position: absolute; top: 132px; right: 44px; width: 270px;
    font-size: 12.5px; line-height: 1.45; color: var(--ink-soft);
  }
  .tagline { margin-bottom: 14px; }
  .contact-row { display: flex; align-items: flex-start; gap: 9px; margin-bottom: 4px; }
  .contact-row svg { flex: none; margin-top: 3px; }
  .person {
    position: absolute; left: 40px; bottom: 38px;
  }
  .person-name { font-size: 24px; font-weight: 700; line-height: 1.1; }
  .person-role { font-size: 13px; color: var(--ink-soft); }
</style>
</head>
<body>
<main class="stage">
  <section class="card card-front">
    <div class="brand"><span class="brand-dot"></span>KIPSY</div>
  </section>

  <section class="card card-back">
    <div class="brand"><span class="brand-dot"></span>KIPSY</div>
    <div class="details">
      <p class="tagline">If it keeps a drink cold or<br>the party going...we do it!</p>
      <div class="contact-row">
        <svg width="11" height="11" viewBox="0 0 24 24" aria-hidden="true"><path fill="#fff" d="M6.6 10.8a15.1 15.1 0 0 0 6.6 6.6l2.2-2.2a1 1 0 0 1 1-.25 11.4 11.4 0 0 0 3.6.57 1 1 0 0 1 1 1V20a1 1 0 0 1-1 1A17 17 0 0 1 3 4a1 1 0 0 1 1-1h3.5a1 1 0 0 1 1 1c0 1.25.2 2.45.57 3.57a1 1 0 0 1-.25 1z"/></svg>
        <span>555.318.4726</span>
      </div>
      <div class="contact-row">
        <svg width="11" height="13" viewBox="0 0 24 28" aria-hidden="true"><path fill="none" stroke="#fff" stroke-width="2.5" d="M12 26s-8-8.5-8-14a8 8 0 0 1 16 0c0 5.5-8 14-8 14z"/><circle cx="12" cy="12" r="3" fill="#fff"/></svg>
        <span>412 E. Carver Avenue,<br>Ste 2207, Tampa, FL. 33917</span>
      </div>
    </div>
    <div class="person">
      <p class="person-name">Dalton Pikes</p>
      <p class="person-role">Founder and CPO</p>
    </div>
  </section>
</main>
</body>
</html>
```